Help design website for "Brightwater Civic Advisors" to advance the common good

Here is the Google doc link that lays out the design:

https://files.plumrivet.example/sheet/d/7QmTzR2wLx9KpVbN4hJcY8sEaUoFdG3iXkMnPq5rWt6/edit?usp=sharing

Here is the Google drive folder with the logos and photos: https://vault.plumrivet.example/open?id=4HkWp9LzQe2TxRvN8mBaYc3DsUoJfG6

The testimonials are being gathered and will be shared by Friday, 1/4.

The winner will also have to migrate the coding files to my hosting site.

Thank you for your help! Looking forward to seeing your designs.

Target Market(s)

Prospective clients

Industry/Entity Type

Non Profit

Coding

Coded - Design and coding required

Number of Pages Required

5+ page

Requirements
Must have
• Noted in the Google doc regarding layout.
Nice to have

```html
<!DOCTYPE html>
<html lang="en">
<head>
<meta charset="utf-8">
<title>Brightwater Civic Advisors</title>
<link rel="stylesheet" href="https://fonts.googleapis.com/css2?family=Alegreya+Sans:wght@400;500;700&family=Open+Sans:wght@400;600;700&display=swap">
<style>
:root{
  --blue:#4a95d6;
  --blue-dark:#3a86c8;
  --ink:#333;
  --muted:#666;
  --light:#f3f3f3;
  --panel:#ededed;
  --white:#fff;
  --line:#d6d6d6;
}
*{box-sizing:border-box;margin:0;padding:0}
html,body{width:1200px;height:3163px;overflow:hidden}
body{font-family:"Open Sans",Arial,sans-serif;color:var(--ink);background:var(--white);position:relative}
.abs{position:absolute}
.topbar{top:0;left:0;width:1200px;height:42px;background:var(--light);font-size:15px;color:#555}
.topbar .item{position:absolute;top:8px;display:flex;align-items:center;gap:10px}
.ring{width:26px;height:26px;border:1.5px solid var(--blue-dark);border-radius:50%;display:flex;align-items:center;justify-content:center}
.nav{top:42px;left:0;width:1200px;height:104px;background:var(--white)}
.btn{display:inline-flex;align-items:center;justify-content:center;background:var(--blue);color:var(--white);border-radius:30px;font-weight:600;font-size:15px;letter-spacing:.3px}
.upload{position:absolute;left:125px;top:32px;width:178px;height:38px;font-size:13px;gap:8px}
.menu{position:absolute;left:346px;top:42px;display:flex;gap:26px;font-size:14px;color:#333}
.brand{position:absolute;display:flex;align-items:center;gap:10px;font-family:"Open Sans",sans-serif;font-weight:600;color:var(--blue-dark)}
.brand .sq{width:26px;height:26px;background:var(--blue-dark)}
.hero{top:146px;left:0;width:1200px;height:529px;background:linear-gradient(180deg,#8a8f94 0%,#6d6560 45%,#4d4a4c 100%);color:var(--white);text-align:center}
.hero .tag{position:absolute;top:150px;width:100%;font-family:"Alegreya Sans",sans-serif;font-size:22px}
.hero h1{position:absolute;top:188px;width:100%;font-size:36px;font-weight:700;letter-spacing:.5px}
.hero p{position:absolute;top:250px;left:350px;width:500px;font-size:16px;font-weight:600;line-height:30px}
.hero .btn{position:absolute;top:333px;left:473px;width:254px;height:50px;font-size:17px}
.about{top:675px;left:0;width:1200px;height:508px;background:var(--panel)}
.portrait{position:absolute;left:100px;top:28px;width:490px;height:480px;background:radial-gradient(ellipse at 55% 45%,#c9a793 0%,#5a4b46 55%,#2e2a2b 100%);border-radius:240px 240px 0 0}
.about h2{position:absolute;left:740px;top:110px;font-family:"Alegreya Sans",sans-serif;font-weight:400;font-size:34px;line-height:40px;color:var(--blue)}
.about .badge{position:absolute;left:648px;top:112px;width:72px;height:72px;border:4px solid var(--blue)}
.about hr{position:absolute;left:648px;top:197px;width:384px;border:0;border-top:1.5px solid #999}
.about p{position:absolute;left:648px;top:218px;width:426px;font-size:16px;line-height:29px;color:#555;text-align:justify}
.services{top:1183px;left:0;width:1200px;height:447px}
.services h2{position:absolute;left:124px;top:85px;font-family:"Alegreya Sans",sans-serif;font-weight:400;font-size:34px;color:var(--blue)}
.services .lead{position:absolute;left:124px;top:142px;width:284px;font-size:13px;line-height:27px;color:#555;text-align:justify}
.services .btn{position:absolute;left:124px;top:298px;width:160px;height:44px;font-size:15px}
.grid{position:absolute;left:448px;top:100px;width:628px;height:284px}
.grid .vl{position:absolute;left:312px;top:0;height:284px;border-left:1px solid var(--line)}
.grid .hl{position:absolute;left:0;top:142px;width:628px;border-top:1px solid var(--line)}
.svc{position:absolute;width:306px;display:flex;gap:14px}
.svc svg{flex:none}
.svc h3{font-size:12px;font-weight:700;margin-bottom:6px;color:#333;white-space:nowrap}
.svc p{font-size:13px;line-height:22px;color:#555}
.testi{top:1630px;left:0;width:1200px;height:523px;background:var(--blue);color:var(--white)}
.testi h2{position:absolute;top:66px;width:100%;text-align:center;font-family:"Alegreya Sans",sans-serif;font-weight:400;font-size:36px}
.card{position:absolute;top:196px;width:309px;height:158px;border-radius:10px;background:rgba(255,255,255,.3);padding:16px 20px 0 20px;font-size:11px;line-height:21px;color:rgba(255,255,255,.85)}
.card.active{background:var(--white);color:#333;top:194px;height:162px}
.card .q{font-family:Georgia,serif;font-size:28px;font-weight:700;line-height:18px;color:#6fb0e6;height:18px;margin-bottom:4px}
.card.active .q{color:var(--blue)}
.card .who{font-size:10px;margin-top:4px;white-space:nowrap}
.avatar{position:absolute;top:-38px;right:110px;width:72px;height:72px;border-radius:50%;border:3px solid var(--white);background:radial-gradient(circle at 50% 40%,#c6a38b,#6a5a55)}
.testi .outline{position:absolute;top:406px;left:457px;width:286px;height:50px;border:2px solid var(--white);border-radius:30px;display:flex;align-items:center;justify-content:center;font-size:15px;font-weight:600}
.media{top:2153px;left:0;width:1200px;height:464px}
.post{position:absolute;top:85px;width:282px}
.post .ph{height:188px}
.post .label{display:inline-block;margin-top:10px;background:var(--blue);color:var(--white);font-size:11px;padding:3px 14px;letter-spacing:.5px}
.post h3{font-size:19px;font-weight:700;line-height:27px;margin-top:8px;color:#333}
.post p{font-size:14px;color:#444;margin-top:6px}
.contact-left{top:2617px;left:0;width:591px;height:470px;background:linear-gradient(160deg,#4a95d6,#3b86c9);color:var(--white)}
.contact-left .intro{position:absolute;left:124px;top:36px;width:360px;font-size:13.5px;line-height:25px}
.contact-left .rule{position:absolute;left:124px;width:306px;border-top:1px solid rgba(255,255,255,.6)}
.contact-left h4{position:absolute;left:124px;top:192px;font-size:20px;font-weight:700}
.contact-left .addr{position:absolute;left:124px;top:232px;font-size:13.5px;line-height:30px}
.contact-right{top:2617px;left:591px;width:609px;height:470px;background:var(--panel)}
.contact-right h2{position:absolute;left:65px;top:52px;font-family:"Alegreya Sans",sans-serif;font-weight:400;font-size:34px;color:var(--blue)}
.field{position:absolute;height:40px;border:1px solid #999;background:var(--white);font-size:13px;color:#555;padding:11px 10px}
.contact-right .btn{position:absolute;left:71px;top:375px;width:137px;height:40px;font-size:15px}
.footer{top:3087px;left:0;width:1200px;height:76px;background:var(--white)}
.footer .copy{position:absolute;left:124px;top:28px;font-size:13px;color:#444}
</style>
</head>
<body>

<header class="abs topbar">
  <div class="item" style="left:124px">
    <span class="ring"><svg width="13" height="13" viewBox="0 0 24 24"><path fill="#3a86c8" d="M6.6 10.8a15 15 0 0 0 6.6 6.6l2.2-2.2c.3-.3.7-.4 1-.2 1.1.4 2.3.6 3.6.6.6 0 1 .4 1 1V20c0 .6-.4 1-1 1A17 17 0 0 1 3 4c0-.6.4-1 1-1h3.5c.6 0 1 .4 1 1 0 1.3.2 2.5.6 3.6.1.3 0 .7-.2 1z"/></svg></span>
    Monday - Friday 9:00 - 18:00
  </div>
  <div class="item" style="left:750px">
    <span class="ring"><svg width="13" height="13" viewBox="0 0 24 24"><path fill="#3a86c8" d="M6.6 10.8a15 15 0 0 0 6.6 6.6l2.2-2.2c.3-.3.7-.4 1-.2 1.1.4 2.3.6 3.6.6.6 0 1 .4 1 1V20c0 .6-.4 1-1 1A17 17 0 0 1 3 4c0-.6.4-1 1-1h3.5c.6 0 1 .4 1 1 0 1.3.2 2.5.6 3.6.1.3 0 .7-.2 1z"/></svg></span>
    +1 888 888 8888
  </div>
  <div class="item" style="left:930px">
    <span class="ring"><svg width="13" height="11" viewBox="0 0 24 18"><rect x="1" y="1" width="22" height="16" fill="none" stroke="#3a86c8" stroke-width="2"/><path d="M1 1l11 9 11-9" fill="none" stroke="#3a86c8" stroke-width="2"/></svg></span>
    info@brightwater.example
  </div>
</header>

<nav class="abs nav">
  <div class="btn upload">
    <svg width="11" height="13" viewBox="0 0 12 14"><rect x="1" y="6" width="10" height="8" rx="1" fill="#fff"/><path d="M3 6V4a3 3 0 0 1 6 0v2" fill="none" stroke="#fff" stroke-width="1.8"/></svg>
    SECURE UPLOAD
  </div>
  <div class="menu"><span>ABOUT</span><span>SERVICES &amp; TESTIMONIALS</span><span>MEDIA &amp; IMPACT</span><span>CONTACT</span></div>
  <div class="brand" style="left:896px;top:34px;font-size:14px;line-height:16px;width:190px">
    <span class="sq"></span><span>Brightwater<br>Civic Advisors</span>
  </div>
</nav>

<section class="abs hero" role="img" aria-label="Group photo of the advisory team standing together in an office">
  <div class="tag">The Common Good</div>
  <h1>BRIGHTWATER CIVIC ADVISORS</h1>
  <p>Sed ut perspiciatis unde omnis iste natus arror vot luptate maccus antium doloremue laudantium</p>
  <div class="btn">BOOK AN APPOINTMENT</div>
</section>

<section class="abs about">
  <div class="portrait" role="img" aria-label="Portrait of the founder"></div>
  <div class="badge"></div>
  <h2>About Brightwater<br>Civic Advisors</h2>
  <hr>
  <p>Brightwater Civic Advisors supports nonprofit organizations and educational institutions to carry out their missions to benefit the wider community. Founder Dana Whitlock is an educator with a 22-year record of demonstrated achievement and leadership roles in nonprofits and educational institutions.</p>
</section>

<section class="abs services">
  <h2>Our Services</h2>
  <p class="lead">Sed ut perspiciatis unde omnis iste natus arrorsit voluptatem accusantium dolorem que laud antium, totam rem aperiam, eaque ipsa quae abillo inventore veritatis quasiar chitectonim ipsam tatema voluptases.</p>
  <div class="btn">VIEW MORE</div>
  <div class="grid">
    <div class="vl"></div><div class="hl"></div>
    <div class="svc" style="left:10px;top:22px">
      <svg width="36" height="36" viewBox="0 0 36 36"><circle cx="18" cy="10" r="7" fill="#555"/><path d="M4 34c0-9 6-14 14-14s14 5 14 14z" fill="#555"/></svg>
      <div><h3>Staff Professional Development</h3><p>Dana has supervised, coached, &amp;<br>mentored hundreds of staff....</p></div>
    </div>
    <div class="svc" style="left:326px;top:22px">
      <svg width="44" height="32" viewBox="0 0 50 36"><path d="M2 10l10-4 8 3 6-3 10 1 12 5-6 14-8-2-6 5-5-4-5 2-6-7-8-1z" fill="none" stroke="#555" stroke-width="3" stroke-linejoin="round"/><path d="M20 12l-6 6 3 3 7-5" fill="none" stroke="#555" stroke-width="2.5"/></svg>
      <div><h3>Community Partnership Development</h3><p>Dana has collaborated with more than<br>250 nonprofits, schools, agencies....</p></div>
    </div>
    <div class="svc" style="left:10px;top:164px">
      <svg width="42" height="36" viewBox="0 0 42 36"><circle cx="10" cy="10" r="5" fill="#555"/><circle cx="32" cy="10" r="5" fill="#555"/><circle cx="21" cy="13" r="6" fill="#555"/><path d="M0 30c0-7 4-11 10-11s8 3 8 3H24s2-3 8-3 10 4 10 11z" fill="#555"/><path d="M9 36c0-8 5-12 12-12s12 4 12 12z" fill="#555"/></svg>
      <div><h3>Group Facilitation &amp; Leadership Training</h3><p>Dana has facilitated student groups,<br>experiential learning activities....</p></div>
    </div>
    <div class="svc" style="left:326px;top:164px">
      <svg width="44" height="40" viewBox="0 0 44 40"><circle cx="16" cy="24" r="9" fill="none" stroke="#555" stroke-width="6" stroke-dasharray="4 3"/><circle cx="16" cy="24" r="3" fill="#555"/><circle cx="33" cy="10" r="6" fill="none" stroke="#555" stroke-width="4" stroke-dasharray="3 2"/></svg>
      <div><h3>Design, Implementation, &amp; Evaluation</h3><p>Dana has launched several programs,<br>take into account best practices....</p></div>
    </div>
  </div>
</section>

<section class="abs testi">
  <h2>Testimonials</h2>
  <div class="card" style="left:93px">
    <div class="avatar" role="img" aria-label="Reviewer photo"></div>
    <div class="q">&ldquo;</div>
    <p>"Dana has an uncanny ability to combine social change theory and real-world practice in truly compelling ways....</p>
    <p class="who">- Martin Hale, VP, Chief Content Officer, WRLN</p>
  </div>
  <div class="card active" style="left:426px">
    <div class="avatar" role="img" aria-label="Reviewer photo"></div>
    <div class="q">&ldquo;</div>
    <p>our team is grateful for Dana's significant contributions to the Civic Futures Network University's (CFN U) Day of Action....</p>
    <p class="who">- Lena Ortiz, Community Manager</p>
  </div>
  <div class="card" style="left:759px">
    <div class="avatar" role="img" aria-label="Reviewer photo"></div>
    <div class="q">&ldquo;</div>
    <p>She organized one of the most successful service projects for our program to date, allowing 1,000 CFU students from around the world....</p>
    <p class="who">- Priya Nandal</p>
  </div>
  <div class="outline">READ OUR CLIENS TESTIMONIALS</div>
</section>

<section class="abs media">
  <article class="post" style="left:148px">
    <div class="ph" role="img" aria-label="Students performing music in a school gym" style="background:linear-gradient(180deg,#8fa6a0,#5d6b66 60%,#3f4a48)"></div>
    <span class="label">ARTICLES</span>
    <h3>Sed ut perspiciatis undeland raentium voluptatum</h3>
    <p>Rasi architecto beatae</p>
  </article>
  <article class="post" style="left:460px">
    <div class="ph" role="img" aria-label="Volunteers working in a city garden" style="background:linear-gradient(180deg,#b9bec4,#8a9088 50%,#5f7a3e)"></div>
    <span class="label">VIDEOS</span>
    <h3>Sed ut perspiciatis undeland raentium voluptatum</h3>
    <p>Rasi architecto beatae</p>
  </article>
  <article class="post" style="left:771px">
    <div class="ph" role="img" aria-label="Speaker at a podium on stage" style="background:linear-gradient(180deg,#2b2523,#3c2a22 60%,#1e1a19)"></div>
    <span class="label">POD CAST</span>
    <h3>Sed ut perspiciatis undeland raentium voluptatum</h3>
    <p>Rasi architecto beatae</p>
  </article>
</section>

<section class="abs contact-left">
  <p class="intro">At vero eos et accusamus et iusto odio dignissimos duci maus qui blanditiis praesentium voluptatum deleniti atque corrupti quos dolores et quas molestias excepturi sint occaecati cupiditate</p>
  <div class="rule" style="top:170px"></div>
  <h4>Address:</h4>
  <div class="addr">Brightwater Civic Advisors<br>Sed ut perspiciatis<br>unde omnis iste natus voluptatem<br>Phone (+1) 888 888 8888<br>Fax (+1) 888 888 8889</div>
  <div class="rule" style="top:405px"></div>
</section>

<section class="abs contact-right">
  <h2>Contact Us</h2>
  <div class="field" style="left:65px;top:104px;width:204px">First Name</div>
  <div class="field" style="left:283px;top:104px;width:204px">Last Name</div>
  <div class="field" style="left:65px;top:158px;width:204px">Organization Name</div>
  <div class="field" style="left:283px;top:158px;width:204px">Email Address</div>
  <div class="field" style="left:65px;top:213px;width:422px">Subject</div>
  <div class="field" style="left:65px;top:270px;width:422px;height:82px">Message</div>
  <div class="btn">SUBMIT</div>
</section>

<footer class="abs footer">
  <p class="copy">Copyright © 2019 Brightwater Civic Advisors. All Rights Reserved.</p>
  <div class="brand" style="left:936px;top:22px;font-size:12px;line-height:14px">
    <span class="sq" style="width:22px;height:22px"></span><span>Brightwater<br>Civic Advisors</span>
  </div>
</footer>

</body>
</html>
```